Calvanto Group Real Estate Company business cards

New business card design, we are generally happy with the basic layout of the existing front of business card, (feel free to change) but require a head shot photo on the back side.

http://www.calvanto.com.au/

Attached logos, and existing business card

------------------------------

Target Market(s)

Real estate

Industry/Entity Type

Real Estate

Contact Information for Business Card

Standard size double sided

Font styles to use
Other font styles liked:
• Futura

Requirements
Must have
• Photo head shot on the back side
Nice to have
• yes
Should not have
• No

```html
<!DOCTYPE html>
<html lang="en">
<head>
<meta charset="utf-8">
<title>Calvanto Group – Business Card</title>
<link rel="stylesheet" href="https://fonts.googleapis.com/css2?family=Arimo:wght@400;700&family=Archivo+Narrow:wght@700&display=swap">
<style>
  :root {
    --backdrop: #d8d4cf;
    --card: #eef0f2;
    --navy: #2a2748;
    --orange: #e07020;
    --text-grey: #3a3a40;
    --photo-top: #c9cdd3;
    --photo-bottom: #2b3146;
    --light: #f4f4f6;
  }
  * { margin: 0; padding: 0; box-sizing: border-box; }
  html, body { width: 1200px; height: 969px; overflow: hidden; background: var(--backdrop); }
  body { position: relative; font-family: "Arimo", Arial, sans-serif; }

  .business-card {
    position: absolute; left: 100px; top: 200px;
    width: 1000px; height: 570px;
    background: var(--card);
    overflow: hidden;
    box-shadow: 0 10px 30px rgba(0,0,0,.18);
  }
  .edge-band { position: absolute; left: 0; top: 0; width: 31px; height: 570px; }

  .brand-name {
    position: absolute; left: 88px; top: 72px;
    font-family: "Arimo", Arial, sans-serif; font-weight: 700;
    font-size: 64px; letter-spacing: -1px; color: var(--navy);
  }
  .services {
    position: absolute; left: 197px; top: 192px;
    font-family: "Archivo Narrow", "Arial Narrow", sans-serif; font-weight: 700;
    font-size: 27px; color: var(--navy); word-spacing: 6px;
  }
  .company-details {
    position: absolute; left: 88px; top: 296px;
    font-size: 27px; line-height: 38px; color: var(--text-grey);
  }
  .contact-list { position: absolute; left: 88px; top: 398px; list-style: none; }
  .contact-list li {
    display: flex; align-items: center; gap: 14px;
    height: 39px; color: var(--text-grey); font-size: 26px;
  }
  .contact-list li.email { font-size: 23px; }
  .contact-list svg { width: 24px; height: 24px; fill: var(--navy); flex: none; }

  .headshot {
    position: absolute; left: 560px; top: 0; width: 440px; height: 570px;
    background: linear-gradient(180deg, var(--photo-top) 0%, #9ba3b0 40%, var(--photo-bottom) 75%);
  }
  .person-name {
    position: absolute; right: 56px; top: 440px;
    font-size: 33px; font-weight: 700; color: var(--orange);
  }
  .person-title {
    position: absolute; right: 56px; top: 486px;
    font-size: 26px; color: var(--light);
  }
</style>
</head>
<body>
  <div class="business-card">
    <svg class="edge-band" viewBox="0 0 31 570" aria-hidden="true">
      <polygon points="0,0 31,0 31,200 0,235" fill="var(--orange)"/>
      <polygon points="0,250 31,215 31,570 0,570" fill="var(--navy)"/>
    </svg>

    <div class="brand-name">Calvanto Group</div>
    <div class="services">Buy | Sell | Rent</div>

    <div class="company-details">
      <p>Calvanto Group</p>
      <p>ABN: 41 502 886 317</p>
    </div>

    <ul class="contact-list">
      <li>
        <svg viewBox="0 0 24 24" aria-hidden="true"><path d="M2 8c0-2 3-4 10-4s10 2 10 4v2h-5V8H7v2H2z M5 12h14l2 8H3z M12 13.5a3 3 0 1 0 0 6 3 3 0 0 0 0-6z"/></svg>
        0412 555 318
      </li>
      <li class="email">
        <svg viewBox="0 0 24 24" aria-hidden="true"><path d="M2 5h20v14H2z" fill="var(--navy)"/><path d="M2 5l10 8 10-8" fill="none" stroke="var(--card)" stroke-width="2"/></svg>
        daniel.tran@calvanto.com.au
      </li>
      <li>
        <svg viewBox="0 0 24 24" aria-hidden="true"><circle cx="12" cy="12" r="10"/><path d="M2 12h20M12 2c3 3 3 17 0 20M12 2c-3 3-3 17 0 20" fill="none" stroke="var(--card)" stroke-width="1.5"/></svg>
        www.calvanto.com.au
      </li>
    </ul>

    <div class="headshot" role="img" aria-label="Head-shot photo of the director in a dark suit and blue tie"></div>
    <div class="person-name">Daniel Tran</div>
    <div class="person-title">Director</div>
  </div>
</body>
</html>
```